Current website re-design to a updated look and feel.

We currently have a website www.brightlanefreight.com that we want to give an updated look and feel to. We are a logistics company that competes with Pellwick, Dm Harrowgate, Quill but on a smaller scale. We want something fresh and updated. We have two locations one in downtown Chicago, IL and one in Palatine IL. We are a fun group that also gets the job done. We know we need pictures of both locations and possibly a video, but we need fresh design ideas. The 'who we are' page is really the only page that we currently want to keep. The 'what we do' page needs to be completely re-done from a look and feel for sure.

Target Market(s)

Anyone who uses Truck transportation to move their product. Mainly US manufacturers.

Industry/Entity Type

Logistics

Number of Pages Required

5+ page

Font styles to use
Sans Serif

Colors
5c91c4
0355a3
d0dfed

Requirements
Must have
• The new design must entice people to want to do business with us. The design must have locations for pictures and at least one video which we know we will have to provide. Design must be easy to navigate.

```html
<!DOCTYPE html>
<html lang="en">
<head>
<meta charset="utf-8">
<title>Brightlane Freight</title>
<link href="https://fonts.googleapis.com/css2?family=Open+Sans:wght@400;600;700&family=Raleway:wght@500;700;800&display=swap" rel="stylesheet">
<style>
:root{
  --blue:#0355a3;
  --sky:#5c91c4;
  --mist:#d0dfed;
  --ink:#3b4450;
  --grey:#6d7680;
  --line:#e3e8ee;
  --white:#ffffff;
  --panel:#f3f6f9;
}
*{box-sizing:border-box;margin:0;padding:0}
html,body{width:1200px;height:2496px;overflow:hidden;background:var(--white)}
body{font-family:"Open Sans",sans-serif;color:var(--ink);font-size:14px;line-height:1.6}
.page{position:relative;width:1200px;height:2496px}
h2,h3,h4{font-family:"Raleway",sans-serif}

/* header */
.site-header{height:88px;display:flex;align-items:center;justify-content:space-between;padding:0 64px;background:var(--white)}
.brand{display:flex;align-items:center;gap:10px;font-family:"Raleway",sans-serif;font-weight:800;font-size:26px;color:var(--blue)}
.brand-dot{width:18px;height:18px;border-radius:50%;background:var(--sky)}
.main-nav{display:flex;align-items:center;gap:28px;font-size:12px;font-weight:700;letter-spacing:.5px;color:var(--blue)}
.login{background:var(--blue);color:var(--white);padding:8px 22px;border-radius:2px}

/* hero */
.hero{position:relative;height:512px;background:linear-gradient(180deg,#8aa3b8 0%,#6f7f8c 35%,#8a5e4a 60%,#4a5a6a 100%)}
.play{position:absolute;left:560px;top:216px;width:80px;height:80px}

/* founder */
.founder{height:320px;display:flex;align-items:flex-start;padding:48px 110px 0 180px;gap:44px}
.founder-photo{flex:0 0 180px;height:180px;border-radius:50%;background:linear-gradient(160deg,#d9dfe6,#a8b4c0);border:6px solid var(--mist)}
.section-title{font-size:24px;font-weight:700;color:var(--sky);margin-bottom:14px}
.section-title b{color:var(--blue)}
.founder p{font-size:12.5px;color:var(--grey);margin-bottom:10px;line-height:1.55}
.signoff{font-style:italic;color:var(--blue);font-weight:600}

/* vision */
.vision{height:460px;display:flex}
.vision-text{flex:0 0 600px;background:var(--panel);padding:36px 40px 0 64px}
.vision-text h2{font-size:22px;font-weight:700;color:var(--sky);line-height:1.2;margin-bottom:24px}
.vision-text h2 b{display:block;color:var(--blue)}
.vision-text h4{font-size:15px;color:var(--blue);margin-bottom:6px}
.vision-text p{font-size:12px;color:var(--grey);margin-bottom:20px;line-height:1.55}
.vision-media{position:relative;flex:1;background:linear-gradient(180deg,#9fb5c8 0%,#7c93a6 55%,#3f4f5c 100%)}
.quote-btn{position:absolute;left:140px;top:280px;background:var(--sky);color:var(--white);font-weight:700;font-size:15px;letter-spacing:1px;padding:14px 34px}
.chat-badge{position:absolute;right:16px;top:18px;display:flex;align-items:center;gap:8px;background:var(--white);border-radius:30px;padding:4px 16px 4px 4px;font-size:13px;font-weight:700;color:var(--blue)}
.chat-badge span{width:34px;height:34px;border-radius:50%;background:var(--mist)}

/* tagline */
.tagline{height:120px;display:flex;flex-direction:column;align-items:center;justify-content:center;gap:8px;background:var(--white)}
.tagline h2{font-size:28px;font-weight:700;color:var(--blue);letter-spacing:1px}
.tagline .mark{display:flex;align-items:center;gap:6px;font-family:"Raleway",sans-serif;font-weight:800;font-size:13px;color:var(--blue)}
.tagline .mark i{width:10px;height:10px;background:var(--sky);display:block}

/* services */
.services{height:560px;display:flex;gap:12px;padding:0 64px;background:var(--panel)}
.service{flex:1;display:flex;flex-direction:column;background:var(--white);border-top:4px solid var(--sky)}
.service .copy{padding:20px 18px;height:210px}
.service h3{font-size:16px;color:var(--blue);margin-bottom:10px}
.service p{font-size:12px;color:var(--grey);line-height:1.55}
.service .photo{flex:1}
.p1{background:linear-gradient(180deg,#6d8fb0,#2b4b6a)}
.p2{background:linear-gradient(180deg,#b7c6d4,#5a6a78)}
.p3{background:linear-gradient(180deg,#c9a86a,#6b5a44)}
.p4{background:linear-gradient(180deg,#dfe4ea,#8f9fae)}

/* updates & contact */
.connect{height:360px;display:flex}
.updates{flex:0 0 600px;background:var(--mist);padding:32px 40px 0 64px}
.updates h2,.contact h2{font-size:20px;font-weight:700;color:var(--blue);margin-bottom:8px}
.updates .lead{font-size:11px;font-style:italic;color:var(--grey);margin-bottom:14px}
.form-row{display:flex;align-items:flex-end;gap:60px}
.field{width:300px;height:26px;background:var(--white);border:1px solid #c5d3e1;font-size:11px;color:#9aa4ae;padding:4px 10px;margin-bottom:8px}
.submit{background:var(--blue);color:var(--white);font-size:11px;font-weight:700;padding:6px 18px;margin-bottom:8px}
.contact{flex:1;display:flex;padding:32px 40px 0 40px;gap:20px;background:var(--white)}
.contact-list{flex:1;font-size:11.5px;color:var(--grey);line-height:1.55}
.contact-list .row{display:flex;gap:8px;margin-bottom:12px}
.contact-list svg{flex:0 0 12px;margin-top:3px}
.map{flex:0 0 200px;height:200px;background:linear-gradient(135deg,#eef2f6,#dbe4ec)}

/* footer */
.site-footer{height:76px;display:flex;align-items:center;justify-content:space-between;padding:0 64px;border-top:1px solid var(--line);font-size:11px;color:var(--grey)}
.badges{display:flex;gap:10px}
.badges span{width:44px;height:44px;border-radius:50%;background:var(--mist)}
.badges span+span{border-radius:4px;width:70px}
.foot-nav{display:flex;gap:22px;font-weight:700;color:var(--blue)}
</style>
</head>
<body>
<div class="page">

<header class="site-header">
  <div class="brand"><span class="brand-dot"></span>Brightlane Freight</div>
  <nav class="main-nav">
    <span>WHAT WE DO</span><span>HOW WE DO IT</span><span>WHO WE ARE</span><span>TRACKING</span><span>CHAT</span><span>CONTACT</span><span class="login">LOGIN</span>
  </nav>
</header>

<section class="hero" role="img" aria-label="Video still of stacked shipping containers at a freight yard">
  <svg class="play" viewBox="0 0 80 80"><circle cx="40" cy="40" r="38" fill="rgba(255,255,255,.25)" stroke="#fff" stroke-width="3"/><path d="M32 25 L58 40 L32 55 Z" fill="#fff"/></svg>
</section>

<section class="founder">
  <div class="founder-photo" role="img" aria-label="Portrait of the company founder"></div>
  <div>
    <h2 class="section-title">WELCOME <b>FROM OUR FOUNDER</b></h2>
    <p>Brightlane Freight welcomes you to our growing family of clients! We have over 20 years of experience in helping people solve their logistics needs from coast to coast. We also provide friendly, exceptional service that makes it easy to do business with us. Give us a call today and experience the difference for yourself!</p>
    <p>Your service commitment begins from the moment you contact us. We appreciate your trust, and we go the extra mile to ensure that your freight is handled with care and expediency. If we move cargo, we want everybody to receive it, saying no excuse will stop us until your freight is delivered without issue!</p>
    <p>Let us take the worry out of your logistics. Relax, we've got this. <span class="signoff">Marion Keats, Founder</span></p>
  </div>
</section>

<section class="vision">
  <div class="vision-text">
    <h2>BRIGHTLANE FREIGHT<b>VISION AND MISSION</b></h2>
    <h4>Our Vision</h4>
    <p>Our vision is to be the premier third party logistics source in North America. We will become premier by providing superior customer service, efficient and cost effective warehousing and distribution solutions. The decisions we make today for hiring, training, technology, strategic vision and customer satisfaction are based on this vision.</p>
    <h4>Our Mission</h4>
    <p>Our mission is to provide the most thorough and satisfying third party logistics experience for its customers. We use leading technology and an industry experienced staff to deliver an unparalleled customer service experience. We leverage the most efficient mode of transportation, and deliver cost effective solutions for warehousing and distribution of your products in every situation.</p>
  </div>
  <div class="vision-media" role="img" aria-label="Photo of a cargo ship loaded with containers at sea">
    <div class="chat-badge"><span></span>Chat Now</div>
    <div class="quote-btn">REQUEST A QUOTE</div>
  </div>
</section>

<section class="tagline">
  <h2>RELAX. WE GOT THIS.</h2>
  <div class="mark"><i></i>Brightlane Freight</div>
</section>

<section class="services">
  <article class="service">
    <div class="copy"><h3>Freight Management</h3><p>We strive for a perfect delivery and promise to be there for anything you may need every step of the way. Don't have to find out more about freight management and how we do it.</p></div>
    <div class="photo p1" role="img" aria-label="Photo of trucks at a port with containers"></div>
  </article>
  <article class="service">
    <div class="copy"><h3>Transportation</h3><p>With a combined 70+ years of industry experience between all employees, we are the logistics company you need to get freight where right. Click here to find out more about our transportation expertise.</p></div>
    <div class="photo p2" role="img" aria-label="Photo of a truck driving on an open highway"></div>
  </article>
  <article class="service">
    <div class="copy"><h3>Warehouse &amp; Distribution</h3><p>Our secure facility can accommodate large or small quantities of product. Our inventory management system provides real time visibility.</p></div>
    <div class="photo p3" role="img" aria-label="Photo of a warehouse with stacked pallets"></div>
  </article>
  <article class="service">
    <div class="copy"><h3>Careers</h3><p>Are you a career looking to work with a great team? Click here to find out why we have the best carrier relationships in the business.</p></div>
    <div class="photo p4" role="img" aria-label="Photo of a warehouse worker holding a clipboard"></div>
  </article>
</section>

<section class="connect">
  <div class="updates">
    <h2>GET UPDATES</h2>
    <p class="lead">We occasionally send out news and industry updates. Sign up and be the first to know what is new.</p>
    <div class="form-row">
      <div>
        <div class="field">First Name</div>
        <div class="field">Last Name</div>
        <div class="field">Organization</div>
        <div class="field">Email</div>
      </div>
      <div class="submit">SUBMIT</div>
    </div>
  </div>
  <div class="contact">
    <div class="contact-list">
      <h2>CONTACT DETAILS</h2>
      <div class="row"><svg width="12" height="14" viewBox="0 0 12 14"><path d="M6 0a5 5 0 0 0-5 5c0 4 5 9 5 9s5-5 5-9a5 5 0 0 0-5-5zm0 7a2 2 0 1 1 0-4 2 2 0 0 1 0 4z" fill="#5c91c4"/></svg><div>88 Harbor Lane, Suite 300<br>Lakeport, IL 60998<br>410 Orchard Way, Suite 12<br>Elm Ridge, IL 60999</div></div>
      <div class="row"><svg width="12" height="12" viewBox="0 0 12 12"><path d="M2 0h3l1 3-2 1a7 7 0 0 0 4 4l1-2 3 1v3a2 2 0 0 1-2 2A10 10 0 0 1 0 2a2 2 0 0 1 2-2z" fill="#5c91c4"/></svg><div>Office Phone: (555) 014-2290<br>Warehouse: (555) 014-2291<br>Fax: (555) 014-2292</div></div>
      <div class="row"><svg width="12" height="10" viewBox="0 0 12 10"><rect width="12" height="10" rx="1" fill="#5c91c4"/><path d="M0 1l6 4 6-4" stroke="#fff" fill="none"/></svg><div>Rates: rates@brightlanefreight.com<br>Warehouse: warehouse@brightlanefreight.com<br>Information: info@brightlanefreight.com</div></div>
    </div>
    <div class="map" role="img" aria-label="Map showing the two office locations"></div>
  </div>
</section>

<footer class="site-footer">
  <div class="badges"><span></span><span></span></div>
  <nav class="foot-nav"><span>WHAT WE DO</span><span>HOW WE DO IT</span><span>WHO WE ARE</span><span>TRACKING</span><span>CHAT</span><span>CONTACT</span></nav>
  <div>Copyright 2017, All Rights Reserved</div>
</footer>

</div>
</body>
</html>
```